MRT Property - Business Cards

Looking for a business card & general letterhead, signage etc design for our new logo.

Colours:
000a20
0056a2
00b5ef
0088ce
68cef2

Fonts:
Poppins
Karla

Please keep look and feel of new brand - example in the zip package I sent.

```html
<!DOCTYPE html>
<html lang="en">
<head>
<meta charset="UTF-8">
<title>MRT Property – Business Cards</title>
<link href="https://fonts.googleapis.com/css2?family=Poppins:wght@400;600;700&family=Karla:wght@400;500&display=swap" rel="stylesheet">
<style>
  :root {
    --navy: #000a20;
    --deep-blue: #0056a2;
    --cyan: #00b5ef;
    --mid-blue: #0088ce;
    --sky: #68cef2;
    --card-dark: #0e1328;
    --paper: #ffffff;
    --ink-grey: #6b6f78;
    --backdrop: #2b2c2f;
  }
  * { margin: 0; padding: 0; box-sizing: border-box; }
  html, body { width: 1200px; height: 952px; overflow: hidden; }
  body {
    background: radial-gradient(ellipse at 55% 45%, #3a3b3e 0%, var(--backdrop) 55%, #1c1d1f 100%);
    display: flex;
    align-items: center;
    justify-content: center;
    gap: 44px;
    font-family: 'Karla', sans-serif;
  }
  .card {
    width: 540px;
    height: 309px;
    border-radius: 4px;
    position: relative;
    overflow: hidden;
    box-shadow: 0 18px 40px rgba(0,0,0,0.45);
  }

  /* Front */
  .card--front { background: var(--card-dark); }
  .front-brand {
    position: absolute;
    left: 40px;
    top: 52px;
    display: flex;
    align-items: center;
    gap: 12px;
  }
  .brand-dot {
    width: 16px; height: 16px;
    border-radius: 50%;
    background: var(--cyan);
  }
  .front-name {
    font-family: 'Poppins', sans-serif;
    font-weight: 700;
    font-size: 34px;
    letter-spacing: 0.5px;
    color: var(--paper);
    line-height: 1;
  }
  .front-graphic {
    position: absolute;
    left: 250px;
    top: 130px;
    right: 0;
    bottom: 0;
    background: linear-gradient(135deg, var(--sky) 0%, var(--cyan) 40%, var(--mid-blue) 100%);
    opacity: 0.9;
  }

  /* Back */
  .card--back { background: var(--paper); }
  .back-brand {
    position: absolute;
    left: 40px;
    top: 78px;
    display: flex;
    align-items: center;
    gap: 10px;
  }
  .brand-square {
    width: 14px; height: 14px;
    background: var(--deep-blue);
  }
  .back-name {
    font-family: 'Poppins', sans-serif;
    font-weight: 700;
    font-size: 24px;
    color: var(--deep-blue);
    line-height: 1;
  }
  .rule { position: absolute; left: 0; right: 0; top: 232px; height: 3px; }
  .rule__dark { position: absolute; left: 0; width: 48%; height: 3px; background: var(--deep-blue); }
  .rule__light { position: absolute; left: 48%; right: 0; top: 4px; height: 5px; background: var(--sky); }

  .contact {
    position: absolute;
    left: 282px;
    top: 56px;
    width: 240px;
  }
  .person { font-family: 'Poppins', sans-serif; font-size: 15px; line-height: 1.1; text-transform: uppercase; }
  .person__given { color: var(--cyan); font-weight: 400; }
  .person__family { color: var(--deep-blue); font-weight: 700; }
  .role { font-size: 11.5px; color: var(--ink-grey); margin-top: 2px; }
  .divider { width: 36px; height: 1px; background: var(--ink-grey); margin: 7px 0 9px; }
  .contact-list { list-style: none; }
  .contact-list li {
    display: flex;
    align-items: flex-start;
    gap: 7px;
    font-size: 10.5px;
    color: var(--ink-grey);
    line-height: 1.35;
    margin-bottom: 3px;
  }
  .icon { flex: none; width: 13px; height: 13px; margin-top: 1px; }
</style>
</head>
<body>

  <section class="card card--front" aria-label="Business card front">
    <div class="front-brand">
      <span class="brand-dot"></span>
      <span class="front-name">MRT Property</span>
    </div>
    <div class="front-graphic" role="img" aria-label="Large brand graphic in sky, cyan and mid blue"></div>
  </section>

  <section class="card card--back" aria-label="Business card back">
    <div class="back-brand">
      <span class="brand-square"></span>
      <span class="back-name">MRT Property</span>
    </div>

    <div class="rule">
      <span class="rule__dark"></span>
      <span class="rule__light"></span>
    </div>

    <div class="contact">
      <p class="person"><span class="person__given">Daniel R. </span><span class="person__family">Hartley</span></p>
      <p class="role">Managing Director</p>
      <div class="divider"></div>
      <ul class="contact-list">
        <li>
          <svg class="icon" viewBox="0 0 13 13"><rect width="13" height="13" rx="2" fill="var(--deep-blue)"/><path d="M6.5 2.5a2.6 2.6 0 0 0-2.6 2.6c0 2 2.6 5 2.6 5s2.6-3 2.6-5a2.6 2.6 0 0 0-2.6-2.6z" fill="#fff"/><circle cx="6.5" cy="5.1" r="1" fill="var(--deep-blue)"/></svg>
          <span>218 Harbor View Lane<br>Portland, OR 97204</span>
        </li>
        <li>
          <svg class="icon" viewBox="0 0 13 13"><rect width="13" height="13" rx="2" fill="var(--cyan)"/><path d="M4 3l1.6-.3.8 2-1 .8a5 5 0 0 0 2.1 2.1l.8-1 2 .8L10 9c-3.7.3-6.3-2.3-6-6z" fill="#fff"/></svg>
          <span>+00 987 654 32</span>
        </li>
        <li>
          <svg class="icon" viewBox="0 0 13 13"><rect width="13" height="13" rx="2" fill="var(--cyan)"/><rect x="2.8" y="4" width="7.4" height="5" fill="none" stroke="#fff" stroke-width="1"/><path d="M2.8 4l3.7 2.8L10.2 4" fill="none" stroke="#fff" stroke-width="1"/></svg>
          <span>info@mrtproperty.com</span>
        </li>
        <li>
          <svg class="icon" viewBox="0 0 13 13"><rect width="13" height="13" rx="2" fill="var(--cyan)"/><path d="M4.5 3v6.5l1.6-1.5 1.1 2.3 1-.5-1.1-2.2h2.2z" fill="#fff"/></svg>
          <span>www.mrtproperty.com</span>
        </li>
      </ul>
    </div>
  </section>

</body>
</html>
```